Need Web Design for Business Process Outsourcing Company (Quorvane)

Quorvane is a business process outsourcing company. Need a simple site similar to http://www.tallowbrinkhire.com/ but with a more professional and credible look. New to the process; not sure where to start and comparing my options. Please let me know what my options are if I choose to go with you. Logo is attached for your reference. Please use same colorway

Reason: I want the final product to be coded. Please confirm you will be able to code final design.

Industry/Entity Type

Business

Coding

Coded - Design and coding required

```html
<!DOCTYPE html>
<html lang="en">
<head>
<meta charset="utf-8">
<title>Quorvane Services</title>
<link href="https://fonts.googleapis.com/css2?family=Cabin:wght@400;500;600;700&family=Arimo:wght@400;700&display=swap" rel="stylesheet">
<style>
:root{
  --navy:#0b4a78;
  --navy-dark:#083c63;
  --brand-blue:#0a8ed0;
  --bright-blue:#1592d4;
  --ink:#2f3338;
  --muted:#6b6f74;
  --white:#ffffff;
  --line:#d8dde2;
  --hero-pink:#e9b9d8;
  --hero-violet:#9b6fb8;
  --photo-slate:#3d4a5e;
}
*{box-sizing:border-box;margin:0;padding:0}
html,body{width:1200px;height:2542px;overflow:hidden}
body{position:relative;background:var(--white);font-family:"Arimo",Arial,sans-serif;color:var(--ink)}
.abs{position:absolute}
.heading{font-family:"Cabin",Arial,sans-serif}

/* navigation */
.site-nav{left:0;top:0;width:1200px;height:63px;background:var(--navy);z-index:5}
.site-nav ul{list-style:none;display:flex;justify-content:center;height:63px;padding-left:4px}
.site-nav li{font-family:"Cabin",Arial,sans-serif;font-weight:600;font-size:16px;color:var(--white);letter-spacing:.3px;line-height:63px;padding:0 24px}
.site-nav li.is-active{background:var(--brand-blue);padding:0 22px}

/* hero + services background */
.hero-art{left:0;top:63px;width:1200px;height:1124px}
.brand{left:0;width:1200px;top:140px;display:flex;justify-content:center;align-items:center;gap:22px}
.brand-square{width:110px;height:110px;background:var(--navy)}
.brand-name{font-family:"Cabin",Arial,sans-serif;font-weight:700;font-size:72px;color:#3a3d42;letter-spacing:-1px}
.hero-title{left:0;width:1200px;top:318px;text-align:center;font-family:"Cabin",Arial,sans-serif;font-weight:600;font-size:78px;color:var(--white);text-shadow:0 3px 8px rgba(40,20,60,.45)}
.hero-lead{left:230px;width:740px;top:414px;text-align:center;font-size:20px;line-height:27px;color:#1d1f24}
.btn-dark{display:flex;align-items:center;justify-content:center;background:var(--navy);color:var(--white);font-family:"Cabin",Arial,sans-serif;font-weight:600;font-size:18px;letter-spacing:.4px}
.hero-cta{left:471px;top:480px;width:260px;height:50px;border-radius:3px}

/* services */
.hub{left:498px;top:573px;width:204px;height:204px;border-radius:50%;background:var(--white);border:5px solid var(--brand-blue);box-shadow:0 0 0 6px rgba(255,255,255,.55);display:flex;align-items:center;justify-content:center;font-family:"Cabin",Arial,sans-serif;font-weight:700;font-size:30px;color:var(--navy)}
.service-node{width:126px;height:126px;border-radius:50%;background:var(--white);border:4px solid rgba(255,255,255,.6);box-shadow:0 0 0 3px #e9eef2 inset;display:flex;align-items:center;justify-content:center}
.service-node .ring{width:104px;height:104px;border-radius:50%;border:3px solid #23374d;display:flex;align-items:center;justify-content:center}
.service-info{width:210px;text-align:center;color:var(--white)}
.service-info h3{font-family:"Cabin",Arial,sans-serif;font-weight:600;font-size:18px;letter-spacing:.3px;margin-bottom:10px}
.service-info p{font-size:14.5px;line-height:23px}

/* global presence */
.presence-band{left:0;top:1090px;width:1200px;height:347px}
.section-title-light{left:0;width:1200px;text-align:center;font-family:"Cabin",Arial,sans-serif;font-weight:600;font-size:38px;color:var(--white);letter-spacing:.5px}
.band-copy{left:175px;width:850px;text-align:center;font-size:16px;line-height:23px;color:var(--white)}
.btn-light{display:flex;align-items:center;justify-content:center;background:var(--white);color:var(--navy);font-weight:700;font-size:15px;border-radius:4px;box-shadow:0 2px 4px rgba(0,0,0,.2)}

/* news */
.news-title{left:0;width:1200px;top:1488px;text-align:center;font-family:"Cabin",Arial,sans-serif;font-weight:600;font-size:40px;color:var(--navy)}
.news-card{top:1563px;width:502px;height:186px;background:var(--white);box-shadow:0 1px 5px rgba(0,0,0,.16);display:flex}
.news-thumb{width:190px;height:186px;flex:none}
.news-body{position:relative;flex:1;padding:30px 22px 0 32px}
.news-body h4{font-family:"Cabin",Arial,sans-serif;font-weight:600;font-size:20px;line-height:27px;color:#1f2226;margin-bottom:10px}
.news-body p{font-size:14px;line-height:23px;color:var(--muted)}
.news-meta{position:absolute;left:32px;right:16px;bottom:0;height:42px;border-top:1px solid #e6e8ea;display:flex;align-items:center;justify-content:space-between;font-size:13px;color:#8a8e93}

/* careers band */
.careers-band{left:0;top:1802px;width:1200px;height:330px}
.careers-title{top:1852px;font-size:34px;font-weight:500}

/* footer area */
.col-title{font-family:"Cabin",Arial,sans-serif;font-weight:500;font-size:30px;color:var(--navy)}
.field{left:78px;width:332px;height:51px;border:1px solid #c9ced3;border-radius:4px;background:var(--white);font-size:15px;color:#555;padding:0 22px;display:flex;align-items:center}
.field.is-focus{border-color:var(--navy)}
.quote-submit{left:78px;top:2397px;width:332px;height:51px;border-radius:3px;font-size:21px;font-weight:500;letter-spacing:.3px}
.map-frame{left:485px;top:2190px;width:196px;height:196px;border-radius:50%;border:3px solid var(--navy)}
.map-link{left:483px;width:200px;top:2420px;text-align:center;font-family:"Cabin",Arial,sans-serif;font-size:19px;color:var(--bright-blue)}
.contact-row{left:790px;display:flex;gap:22px;font-size:15px;line-height:23px;color:#333}
.contact-row svg{flex:none}
.contact-name{font-family:"Cabin",Arial,sans-serif;font-weight:600;font-size:19px;color:#222;letter-spacing:.3px;margin-bottom:2px}
.social{top:2402px;width:41px;height:41px}
.copyright{left:0;top:2492px;width:1200px;height:50px;background:var(--navy);color:var(--white);font-family:"Cabin",Arial,sans-serif;font-size:13px;display:flex;align-items:center;justify-content:center}
.copyright span{color:#3fb2ee;margin:0 4px}
</style>
</head>
<body>

<nav class="site-nav abs">
  <ul>
    <li class="is-active">HOME</li><li>ABOUT</li><li>SERVICES</li><li>STRATEGY</li><li>EXPERIENCE</li><li>SECURITY</li><li>NEWS</li><li>CONTACT</li>
  </ul>
</nav>

<svg class="hero-art abs" width="1200" height="1124" viewBox="0 0 1200 1124" role="img" aria-label="Photo of a smiling businesswoman over a city highway, blending into a photo of a business handshake at a meeting table">
  <defs>
    <linearGradient id="heroGlow" x1="0" y1="0" x2="1" y2="0.3">
      <stop offset="0" stop-color="#c9a9c9"/>
      <stop offset="0.35" stop-color="#f2dbe9"/>
      <stop offset="0.7" stop-color="#e8b3d4"/>
      <stop offset="1" stop-color="#b07ab8"/>
    </linearGradient>
    <linearGradient id="meetingTone" x1="0" y1="0" x2="0" y2="1">
      <stop offset="0" stop-color="#2a3a52"/>
      <stop offset="0.55" stop-color="#4b5a70"/>
      <stop offset="1" stop-color="#7d8a9c"/>
    </linearGradient>
  </defs>
  <rect width="1200" height="1124" fill="url(#meetingTone)"/>
  <path d="M0 0H1200V540C900 590 780 690 600 690C420 690 300 590 0 520Z" fill="url(#heroGlow)"/>
  <path d="M0 470C300 560 420 650 600 660C420 670 300 580 0 520Z" fill="#9b7bb0" opacity=".5"/>
</svg>

<div class="brand abs">
  <div class="brand-square"></div>
  <div class="brand-name">Quorvane Services</div>
</div>
<h1 class="hero-title abs">We Offer SOLUTIONS</h1>
<p class="hero-lead abs">Lorem Ipsum is simply dummy text of the printing and typesetting industry. Lorem Ipsum has been the industry's standard dummy text ever since the 1500s</p>
<div class="hero-cta btn-dark abs">GET A FREE QUOTE</div>

<svg class="abs" style="left:0;top:0" width="1200" height="1100" viewBox="0 0 1200 1100" aria-hidden="true">
  <g stroke="#ffffff" stroke-width="2.5">
    <line x1="600" y1="675" x2="229" y2="759"/>
    <line x1="600" y1="675" x2="412" y2="837"/>
    <line x1="600" y1="675" x2="600" y2="868"/>
    <line x1="600" y1="675" x2="793" y2="837"/>
    <line x1="600" y1="675" x2="975" y2="759"/>
  </g>
</svg>

<div class="hub abs">Quorvane</div>

<!-- customer service -->
<div class="service-node abs" style="left:166px;top:696px"><div class="ring">
  <svg width="56" height="56" viewBox="0 0 56 56" fill="none" stroke="#1d9ad6" stroke-width="3"><circle cx="28" cy="26" r="13"/><path d="M12 28a16 16 0 0 1 32 0"/><rect x="8" y="24" width="6" height="12" rx="2"/><rect x="42" y="24" width="6" height="12" rx="2"/><path d="M45 36c0 8-8 10-14 10"/><path d="M12 54c3-8 9-11 16-11s13 3 16 11" stroke="#23374d"/></svg>
</div></div>
<div class="service-info abs" style="left:124px;top:844px"><h3>CUSTOMER SERVICE</h3><p>Lorem Ipsum is simply dummy text of the printing and typesetting industry.</p></div>

<!-- ecommerce -->
<div class="service-node abs" style="left:349px;top:774px"><div class="ring">
  <svg width="54" height="54" viewBox="0 0 54 54" fill="none" stroke="#23374d" stroke-width="3"><path d="M4 8h8l6 26h26l5-18H15"/><circle cx="22" cy="43" r="4" stroke="#1d9ad6"/><circle cx="40" cy="43" r="4" stroke="#1d9ad6"/></svg>
</div></div>
<div class="service-info abs" style="left:307px;top:927px"><h3>ECOMMERCE</h3><p>Lorem Ipsum is simply dummy text of the printing and typesetting industry.</p></div>

<!-- creative -->
<div class="service-node abs" style="left:537px;top:805px"><div class="ring">
  <svg width="54" height="54" viewBox="0 0 54 54" fill="none" stroke="#23374d" stroke-width="3"><path d="M27 12a12 12 0 0 0-7 22v6h14v-6a12 12 0 0 0-7-22z"/><path d="M21 45h12M23 50h8"/><path d="M27 2v5M10 9l4 4M44 9l-4 4M4 25h5M45 25h5" stroke="#1d9ad6"/></svg>
</div></div>
<div class="service-info abs" style="left:495px;top:958px"><h3>CREATIVE</h3><p>Lorem Ipsum is simply dummy text of the printing and typesetting industry.</p></div>

<!-- it solutions -->
<div class="service-node abs" style="left:730px;top:774px"><div class="ring">
  <svg width="58" height="54" viewBox="0 0 58 54" fill="none" stroke="#23374d" stroke-width="3"><rect x="4" y="6" width="50" height="32" rx="2"/><path d="M29 38v8M18 48h22"/><circle cx="22" cy="22" r="5" stroke="#1d9ad6"/><circle cx="36" cy="20" r="4" stroke="#1d9ad6"/></svg>
</div></div>
<div class="service-info abs" style="left:688px;top:927px"><h3>IT SOLUTIONS</h3><p>Lorem Ipsum is simply dummy text of the printing and typesetting industry.</p></div>

<!-- human resources -->
<div class="service-node abs" style="left:912px;top:696px"><div class="ring">
  <svg width="56" height="56" viewBox="0 0 56 56" fill="none" stroke="#23374d" stroke-width="3"><circle cx="30" cy="22" r="14"/><path d="M20 32L6 46"/><circle cx="30" cy="18" r="4" stroke="#1d9ad6"/><path d="M22 30c2-5 14-5 16 0" stroke="#1d9ad6"/><path d="M10 52c2-4 5-6 8-6M50 52c-2-4-5-6-8-6"/></svg>
</div></div>
<div class="service-info abs" style="left:870px;top:844px"><h3>HUMAN RESOURCES</h3><p>Lorem Ipsum is simply dummy text of the printing and typesetting industry.</p></div>

<!-- global presence -->
<svg class="presence-band abs" width="1200" height="347" viewBox="0 0 1200 347" aria-hidden="true">
  <path d="M0 97C300 18 450 4 600 4C750 4 900 18 1200 97V347H0Z" fill="var(--brand-blue)"/>
</svg>
<h2 class="section-title-light abs" style="top:1154px">GLOBAL PRESENCE</h2>
<p class="band-copy abs" style="top:1218px">Lorem Ipsum is simply dummy text of the printing and typesetting industry. Lorem Ipsum has been the industry's standard dummy text ever since the 1500s, when an unknown printer took a galley of type and scrambled it to make a type specimen book. It has survived not only five centuries, but also the leap into electronic typesetting, remaining essentially unchanged.</p>
<div class="btn-light abs" style="left:534px;top:1334px;width:132px;height:51px">READ MORE</div>

<!-- latest news -->
<h2 class="news-title abs">LATEST NEWS</h2>
<article class="news-card abs" style="left:76px">
  <div class="news-thumb" role="img" aria-label="Photo of colleagues meeting around a table with laptops" style="background:linear-gradient(135deg,#d9d4cf,#9c8a78 60%,#5a4a3e)"></div>
  <div class="news-body">
    <h4>Lorem Ipsum is simply.</h4>
    <p>Lorem Ipsum is simply dummy text of the printing and typesetting industry.</p>
    <div class="news-meta"><span>Jul 14, 2016</span><svg width="22" height="18" viewBox="0 0 22 18" fill="none" stroke="#1592d4" stroke-width="2"><path d="M13 2l7 6-7 6M20 8H10C5 8 2 11 2 16"/></svg></div>
  </div>
</article>
<article class="news-card abs" style="left:622px">
  <div class="news-thumb" role="img" aria-label="Illustration of arrows rising upward from a road" style="background:linear-gradient(180deg,#eef1f3,#b9c4cb 60%,#6e8592)"></div>
  <div class="news-body">
    <h4>Lorem Ipsum is simply dummy text of the printing and typesetting industry?</h4>
    <div class="news-meta"><span>Jul 14, 2016</span><svg width="22" height="18" viewBox="0 0 22 18" fill="none" stroke="#1592d4" stroke-width="2"><path d="M13 2l7 6-7 6M20 8H10C5 8 2 11 2 16"/></svg></div>
  </div>
</article>

<!-- careers -->
<svg class="careers-band abs" width="1200" height="330" viewBox="0 0 1200 330" aria-hidden="true">
  <path d="M0 0H1200V255C900 310 750 325 600 325C450 325 300 310 0 255Z" fill="var(--brand-blue)"/>
</svg>
<h2 class="section-title-light careers-title abs">Passionate about engaging with clients &amp; growing business?</h2>
<p class="band-copy abs" style="top:1916px">Lorem Ipsum is simply dummy text of the printing and typesetting industry. Lorem Ipsum has been the industry's standard dummy text ever since the 1500s, when an unknown printer took a galley of type and scrambled it to make a type specimen book. It has survived not only five centuries, but also the leap into electronic typesetting, remaining essentially unchanged.</p>
<div class="btn-light abs" style="left:522px;top:2032px;width:154px;height:50px">APPLY WITH US!</div>

<!-- quote form -->
<h3 class="col-title abs" style="left:80px;top:2162px">Send Me a Quote</h3>
<div class="field is-focus abs" style="top:2220px">Name:</div>
<div class="field abs" style="top:2278px">Phone:</div>
<div class="field abs" style="top:2336px">E-Mail:</div>
<div class="quote-submit btn-dark abs">REQUEST A QUOTE</div>

<!-- map -->
<div class="map-frame abs" role="img" aria-label="Street map of the office location" style="background:radial-gradient(circle at 45% 45%,#f3efe2,#e0dccb 60%,#c9d9b8)"></div>
<div class="map-link abs">View Large Map</div>

<!-- contact -->
<h3 class="col-title abs" style="left:792px;top:2162px">Contact Us</h3>
<div class="contact-row abs" style="top:2218px">
  <svg width="24" height="30" viewBox="0 0 24 30" fill="none" stroke="#1592d4" stroke-width="2.5"><path d="M12 2v26M3 6h16l3 3-3 3H3zM8 14H20"/></svg>
  <div><div class="contact-name">Quorvane SERVICES</div>123 Building Name, Street Name,<br>City, Country - Zipcode</div>
</div>
<div class="contact-row abs" style="top:2302px">
  <svg width="24" height="24" viewBox="0 0 24 24" fill="none" stroke="#1592d4" stroke-width="2"><path d="M6 2l4 5-2 3c1 3 3 5 6 6l3-2 5 4-2 4C10 22 2 14 2 4z"/></svg>
  <div>+12 34 567 890</div>
</div>
<div class="contact-row abs" style="top:2350px">
  <svg width="24" height="20" viewBox="0 0 24 20" fill="none" stroke="#1592d4" stroke-width="2"><rect x="2" y="3" width="20" height="14"/><path d="M2 3l10 8 10-8"/></svg>
  <div>info@quorvaneservices.com</div>
</div>
<div class="social abs" style="left:790px;background:#3b5aa0"></div>
<div class="social abs" style="left:842px;background:#1eaae6"></div>
<div class="social abs" style="left:893px;background:#d6412f"></div>
<div class="social abs" style="left:946px;background:#0d77b5"></div>

<footer class="copyright abs">@ <span>Quorvane SERVICES</span> - 2016. All Rights Reserved.</footer>

</body>
</html>
```